Need help in designing new business card utilizing our new logo.

BuildMark Solutions works with Construction Business Owners, Managers & IT Professionals to strengthen software usage and increase user productivity.

Our Construction Accounting and Mobile Field Management Software Clients engage with us in the following areas:

New Software Implementations
Software Re-Implementations
Redesigning Software Usage at the User Level
Project Coordination & Management
Continued Software Support

Old tag line:
Weighing Options - Implementing Solutions

www.buildmark-solutions.example

Ridge 4 is a product, but not needed for a new business card.

```html
<!DOCTYPE html>
<html lang="en">
<head>
<meta charset="utf-8">
<title>BuildMark Solutions – Business Card</title>
<link href="https://fonts.googleapis.com/css2?family=Montserrat:wght@500&family=Oswald:wght@600&family=Questrial&display=swap" rel="stylesheet">
<style>
  :root {
    --stage: #3a3b3e;
    --card-dark: #2c2f37;
    --card-light: #ffffff;
    --brand-blue: #2e3192;
    --accent-blue: #3d4fd6;
    --soft-grey: #c5c7cb;
    --ink: #2a2c33;
    --on-dark: #f2f2f4;
  }
  html, body {
    margin: 0;
    width: 1200px;
    height: 800px;
    overflow: hidden;
    background: var(--stage);
  }
  .canvas {
    position: relative;
    width: 1200px;
    height: 800px;
  }
  .card {
    position: absolute;
    width: 580px;
    height: 331px;
    overflow: hidden;
    box-shadow: 0 10px 28px rgba(0,0,0,.45);
  }
  .card--back {
    left: 90px;
    top: 60px;
    background: var(--card-dark);
  }
  .card--front {
    left: 530px;
    top: 410px;
    background: var(--card-light);
  }

  /* brand name lockup */
  .brand {
    position: absolute;
    display: flex;
    align-items: center;
    gap: 12px;
  }
  .brand__mark {
    width: 30px;
    height: 30px;
    background: var(--brand-blue);
  }
  .brand__name {
    font-family: "Montserrat", sans-serif;
    font-weight: 500;
    font-size: 30px;
    letter-spacing: 0.5px;
    color: var(--brand-blue);
    white-space: nowrap;
  }
  .card--back .brand {
    left: 50%;
    top: 128px;
    transform: translateX(-50%);
  }
  .card--back .brand__name { color: var(--accent-blue); }
  .card--back .brand__mark { background: var(--accent-blue); }
  .back__web {
    position: absolute;
    left: 0;
    right: 0;
    bottom: 28px;
    margin: 0;
    text-align: center;
    font-family: "Questrial", sans-serif;
    font-size: 15px;
    letter-spacing: 0.6px;
    color: var(--soft-grey);
  }

  /* front */
  .front__shapes {
    position: absolute;
    inset: 0;
  }
  .card--front .brand {
    left: 34px;
    top: 118px;
  }
  .card--front .brand__name { font-size: 26px; }
  .front__person {
    position: absolute;
    right: 30px;
    top: 20px;
    text-align: right;
  }
  .front__name {
    font-family: "Oswald", sans-serif;
    font-weight: 600;
    font-size: 30px;
    line-height: 1;
    color: var(--ink);
    letter-spacing: 0.3px;
  }
  .front__role {
    font-family: "Questrial", sans-serif;
    font-size: 17px;
    color: var(--ink);
    margin-top: 3px;
  }
  .front__address {
    position: absolute;
    left: 44px;
    top: 222px;
    font-style: normal;
    font-family: "Questrial", sans-serif;
    font-size: 15px;
    line-height: 1.35;
    color: var(--ink);
  }
  .front__contact {
    position: absolute;
    right: 18px;
    top: 222px;
    list-style: none;
    margin: 0;
    padding: 0;
    font-family: "Questrial", sans-serif;
    font-size: 11px;
    line-height: 18px;
    color: var(--on-dark);
    text-align: right;
    white-space: nowrap;
  }
  .front__contact li {
    display: flex;
    justify-content: flex-end;
    align-items: center;
    gap: 8px;
  }
  .icon {
    width: 11px;
    height: 11px;
    flex: none;
  }
</style>
</head>
<body>
<main class="canvas">

  <section class="card card--back" aria-label="Card back">
    <div class="brand">
      <span class="brand__mark"></span>
      <span class="brand__name">BuildMark Solutions</span>
    </div>
    <p class="back__web">www.buildmark-solutions.example</p>
  </section>

  <section class="card card--front" aria-label="Card front">
    <svg class="front__shapes" viewBox="0 0 580 331" width="580" height="331" aria-hidden="true">
      <path d="M0,286 C110,280 190,295 250,331 L0,331 Z" fill="var(--soft-grey)"/>
      <path d="M0,300 C100,296 170,308 215,331 L0,331 Z" fill="var(--card-light)"/>
      <path d="M580,95 C480,100 440,170 395,235 C355,290 300,312 200,331 L580,331 Z" fill="var(--card-dark)"/>
      <path d="M580,82 C470,88 428,160 382,228 C340,290 280,308 160,320" fill="none" stroke="var(--brand-blue)" stroke-width="6"/>
    </svg>

    <div class="front__person">
      <div class="front__name">DANA R. WHITFIELD</div>
      <div class="front__role">Owner</div>
    </div>

    <div class="brand">
      <span class="brand__mark"></span>
      <span class="brand__name">BuildMark Solutions</span>
    </div>

    <address class="front__address">
      14b Foundry Lane - PMB 118<br>
      Clearwater Falls NY 12000
    </address>

    <ul class="front__contact">
      <li>866-555-0142 ext.100
        <svg class="icon" viewBox="0 0 12 12"><path d="M3 1l2 2.5-1.2 1.3c.6 1.4 1.6 2.4 3 3L8 6.6 10.5 8.5 9.6 10.8C5 10.6 1.4 7 1.2 2.4Z" fill="var(--accent-blue)"/></svg>
      </li>
      <li>518-555-0179
        <svg class="icon" viewBox="0 0 12 12"><rect x="3" y="0.5" width="6" height="11" rx="1" fill="none" stroke="var(--accent-blue)" stroke-width="1.4"/></svg>
      </li>
      <li>www.buildmark-solutions.example
        <svg class="icon" viewBox="0 0 12 12"><circle cx="5" cy="5" r="3.6" fill="none" stroke="var(--accent-blue)" stroke-width="1.6"/><path d="M7.6 7.6L11 11" stroke="var(--accent-blue)" stroke-width="1.8"/></svg>
      </li>
      <li>dana@buildmark-solutions.example
        <svg class="icon" viewBox="0 0 12 12"><rect x="0.5" y="2" width="11" height="8" fill="var(--accent-blue)"/><path d="M0.5 2l5.5 4.5L11.5 2" fill="none" stroke="var(--card-dark)" stroke-width="1"/></svg>
      </li>
    </ul>
  </section>

</main>
</body>
</html>
```